Design a single page Shopify store web page

We are looking to have a page designed for a single page Shopify store with 2 products. We already have a basic structure that we like, though we are open to suggestions. We are looking for somebody to provide a design/color scheme that we can then implement using Shopify's templating system. We can handle the implementation(HTML / CSS / jS) as we already have 2 web developers on the team, but have not been able to find a design we liked.

The job would consist of providing a mockup (photoshop or otherwise) and any vector graphics you choose to create for the site (we can provide product photos and other images).

You can also look at http://brickdune.com.au for some of our design direction we have used so far

Target Market(s)

Young Australian Males (18 - 49)

Industry/Entity Type

Store

Number of Pages Required

1 page

Font styles to use
Serif
Sans Serif

Requirements
Must have
• Single Page Design
• E-commerce Product Purchase
• Manly (whatever interpretation of that you have)

```html
<!DOCTYPE html>
<html lang="en">
<head>
<meta charset="utf-8">
<title>Brick Dune – Underwear &amp; Socks Plans</title>
<link rel="stylesheet" href="https://fonts.googleapis.com/css2?family=Lato:wght@400;700;900&family=Dancing+Script:wght@400&display=swap">
<style>
:root{
  --ink:#141414;
  --ink-soft:#1c1c1c;
  --white:#ffffff;
  --sky:#00a8e8;
  --wood-dark:#3b2516;
  --wood-mid:#7a5235;
  --wood-light:#a3764f;
  --comfort:#e8474a;
  --comfort-badge:#17a65b;
  --style:#f26a24;
  --style-badge:#f7941d;
  --go:#8cc63f;
  --field:#eeeeee;
  --text-grey:#333333;
}
*{margin:0;padding:0;box-sizing:border-box}
html,body{width:1200px;height:3141px;overflow:hidden}
body{position:relative;font-family:"Lato",Arial,sans-serif;color:var(--white);background:var(--ink)}

/* header */
.site-header{position:absolute;left:0;top:0;width:1200px;height:105px;background:var(--ink)}
.brand{position:absolute;left:136px;top:14px;width:126px;height:126px;border-radius:50%;background:var(--white);border:4px solid var(--ink);display:flex;align-items:center;justify-content:center;text-align:center;color:var(--ink);font-weight:900;font-size:24px;line-height:24px;z-index:3}
.nav a{position:absolute;top:40px;color:var(--white);font-size:17px;font-weight:700;text-decoration:none}
.nav-underline{position:absolute;left:404px;top:98px;width:141px;height:5px;background:var(--sky)}
.signup{position:absolute;left:944px;top:36px;width:118px;height:33px;border:2px solid var(--sky);color:var(--sky);font-size:13px;font-weight:700;display:flex;align-items:center;justify-content:center}

/* wood bands */
.wood{position:absolute;left:0;width:1200px;background:linear-gradient(90deg,var(--wood-dark) 0%,var(--wood-mid) 12%,var(--wood-light) 25%,var(--wood-mid) 38%,var(--wood-light) 52%,var(--wood-mid) 66%,var(--wood-light) 80%,var(--wood-mid) 92%,var(--wood-dark) 100%)}

/* hero */
.hero-photo{position:absolute;left:138px;top:151px;width:924px;height:550px;background:linear-gradient(100deg,#7d7d80 0%,#b7b7ba 35%,#e4e4e6 60%,#f4f4f4 100%)}
.hero-bubble{position:absolute;left:599px;top:178px;width:440px;height:440px;border-radius:50%;background:var(--sky)}
.hero-product{position:absolute;left:670px;top:185px;width:290px;height:170px;background:linear-gradient(160deg,#3cb7d9,#1b7fa8)}
.hero-copy{position:absolute;left:670px;top:425px;width:300px;font-size:25px;font-weight:700;line-height:29px;text-align:center}
.shop-btn{position:absolute;left:759px;top:568px;width:121px;height:42px;border:3px solid var(--ink);border-radius:6px;color:var(--ink);font-size:16px;font-weight:700;display:flex;align-items:center;justify-content:center}
.slider-arrow{position:absolute;top:387px;width:76px;height:76px;border-radius:50%;background:rgba(235,235,235,.9)}
.slider-arrow svg{position:absolute;left:26px;top:26px}

/* how it works */
.how{position:absolute;left:0;top:750px;width:1200px;height:412px;background:var(--ink-soft)}
.section-title{position:absolute;left:0;width:1200px;text-align:center;font-weight:700;font-size:21px}
.step{position:absolute;width:300px;text-align:center}
.step svg{display:block;margin:0 auto}
.step h3{font-family:"Dancing Script",cursive;font-weight:400;color:var(--sky);font-size:27px;margin-top:18px}
.step p{font-size:16px;line-height:24px;margin-top:18px}
.step-arrow{position:absolute;top:1008px}

/* plans */
.plan{position:absolute;top:1273px;width:452px;height:423px;box-shadow:0 8px 14px rgba(0,0,0,.45)}
.plan--comfort{left:138px;background:var(--comfort)}
.plan--style{left:605px;background:var(--style)}
.plan-badge{position:absolute;left:8px;top:-17px;width:122px;height:122px;border-radius:50%;display:flex;align-items:center;justify-content:center;font-size:21px;font-weight:700}
.plan--comfort .plan-badge{background:var(--comfort-badge)}
.plan--style .plan-badge{background:var(--style-badge)}
.plan-photo{position:absolute;left:17px;top:113px;width:272px;height:272px;border:6px solid rgba(255,255,255,.35)}
.plan--comfort .plan-photo{background:linear-gradient(135deg,#2d3d48,#1e7f9a 50%,#222)}
.plan--style .plan-photo{background:linear-gradient(135deg,#1d2a38,#3e4650 50%,#a76a3a)}
.plan-option{position:absolute;left:308px;width:138px;height:46px;font-size:12px;font-weight:700;display:flex;align-items:center;justify-content:center;box-shadow:0 2px 3px rgba(0,0,0,.2)}
.plan--comfort .plan-option{background:var(--comfort-badge)}
.plan--style .plan-option{background:var(--style-badge)}
.plan-price{position:absolute;left:306px;top:288px;font-size:52px;font-weight:700}
.get-it{position:absolute;left:308px;top:356px;width:103px;height:34px;background:var(--go);font-size:21px;font-weight:700;display:flex;align-items:center;justify-content:center}

/* perks */
.perks{position:absolute;left:0;top:1748px;width:1200px;height:84px;background:rgba(20,20,20,.78)}
.perk{position:absolute;top:20px;display:flex;align-items:center;gap:14px;font-size:13px}
.perk-icon{width:44px;height:44px;border:2px solid var(--white);border-radius:50%;display:flex;align-items:center;justify-content:center}

/* faq */
.faq{position:absolute;left:0;top:1832px;width:1200px;height:580px;background:var(--sky)}
.faq-item{position:absolute;width:270px;text-align:center}
.faq-item h4{font-size:16px;font-weight:700;line-height:23px}
.faq-item p{font-size:12px;line-height:23px;margin:34px auto 0;width:258px}
.faq-item p.tight{margin-top:10px}
.dots{position:absolute;left:550px;top:536px;display:flex;gap:9px}
.dots span{width:15px;height:15px;border-radius:50%;background:var(--white)}
.dots span.on{background:var(--ink)}

/* contact */
.contact{position:absolute;left:0;top:2412px;width:1200px;height:610px;background:var(--white);color:var(--text-grey)}
.contact .section-title{color:var(--ink);top:34px;font-size:23px}
.field-label{position:absolute;left:165px;font-size:12px;color:var(--ink)}
.field{position:absolute;left:165px;width:361px;background:var(--field);border:1px solid #e4e4e4;border-radius:5px}
.submit{position:absolute;left:165px;top:524px;width:84px;height:29px;background:var(--sky);color:var(--white);border-radius:4px;font-size:12px;font-weight:700;display:flex;align-items:center;justify-content:center;gap:4px}
.divider{position:absolute;left:553px;top:105px;width:1px;height:360px;background:#dddddd}
.col-title{position:absolute;left:595px;color:var(--sky);font-size:16px;font-weight:700}
.map{position:absolute;left:595px;top:153px;width:425px;height:185px;border:2px solid #cccccc;background:linear-gradient(120deg,#dfe7d8,#efe9dc 50%,#cfe3c6)}
.address{position:absolute;left:595px;top:418px;font-size:13px;line-height:24px;color:var(--ink)}

/* footer */
.site-footer{position:absolute;left:0;top:3022px;width:1200px;height:119px;background:var(--ink)}
.footer-links{position:absolute;left:142px;top:34px;font-size:12px;font-weight:700}
.footer-links span{margin:0 9px}
.copyright{position:absolute;left:142px;top:69px;font-size:12px;font-weight:700}
.footer-head{position:absolute;top:34px;font-size:12px}
.pay-cards{position:absolute;left:670px;top:61px;display:flex;gap:5px}
.pay-cards span{width:32px;height:20px;border-radius:2px;background:#dddddd}
.pay-cards span:nth-child(2){background:#1a4fa0}
.pay-cards span:nth-child(4){background:#3f7ec4}
.pay-cards span:nth-child(5){background:#e85a1c}
.socials{position:absolute;left:951px;top:61px;display:flex;gap:9px}
.socials span{width:25px;height:25px;border-radius:50%;border:1px solid #5a5a5a;background:#262626}
</style>
</head>
<body>

<header class="site-header">
  <nav class="nav">
    <a style="left:421px">How It Works</a>
    <a style="left:600px">Plans</a>
    <a style="left:713px">FAQ</a>
    <a style="left:820px">Contact Us</a>
  </nav>
  <div class="nav-underline"></div>
  <div class="signup">SIGN UP NOW !</div>
</header>
<div class="brand">BRICK<br>DUNE</div>

<!-- hero -->
<div class="wood" style="top:105px;height:645px" role="img" aria-label="Dark timber plank wall background"></div>
<div class="hero-photo" role="img" aria-label="Photo of a man modelling white briefs against a light grey backdrop"></div>
<div class="hero-bubble"></div>
<div class="hero-product" role="img" aria-label="Photo of folded blue trunks in retail packaging"></div>
<p class="hero-copy">Automate your life New<br>underwear and socks<br>delivered to your door<br>when you need it</p>
<div class="shop-btn">SHOP NOW</div>
<div class="slider-arrow" style="left:67px"><svg width="24" height="24" viewBox="0 0 24 24"><path d="M15 4 L7 12 L15 20" fill="none" stroke="#1a9ad6" stroke-width="3"/></svg></div>
<div class="slider-arrow" style="left:1034px"><svg width="24" height="24" viewBox="0 0 24 24"><path d="M9 4 L17 12 L9 20" fill="none" stroke="#1a9ad6" stroke-width="3"/></svg></div>

<!-- how it works -->
<section class="how">
  <h2 class="section-title" style="top:36px;color:var(--sky)">HOW IT WORKS</h2>
</section>
<div class="step" style="left:91px;top:866px">
  <svg width="76" height="68" viewBox="0 0 76 68"><path d="M6 12 H40 M6 12 V62 H56 V34" fill="none" stroke="#fff" stroke-width="5"/><path d="M30 46 L34 32 L62 4 L72 14 L44 42 Z" fill="#fff"/></svg>
  <h3>Choose a Plan</h3>
  <p>There will be plans for all<br>budgets and styles.</p>
</div>
<div class="step" style="left:451px;top:866px">
  <svg width="56" height="68" viewBox="0 0 56 68"><path d="M2 2 H38 L54 18 V66 H2 Z" fill="#fff"/><g fill="#141414"><rect x="12" y="24" width="5" height="5"/><rect x="21" y="24" width="24" height="5"/><rect x="12" y="35" width="5" height="5"/><rect x="21" y="35" width="24" height="5"/><rect x="12" y="46" width="5" height="5"/><rect x="21" y="46" width="24" height="5"/></g></svg>
  <h3>Choose How Often</h3>
  <p>Decide whether you would like<br>to receive new packages every<br>3 or 6 months.</p>
</div>
<div class="step" style="left:784px;top:866px">
  <svg width="72" height="68" viewBox="0 0 72 68"><rect x="4" y="20" width="64" height="14" fill="#fff"/><rect x="9" y="38" width="54" height="28" fill="#fff"/><rect x="32" y="20" width="8" height="46" fill="#141414"/><path d="M36 18 C24 2 10 6 18 16 Z M36 18 C48 2 62 6 54 16 Z" fill="none" stroke="#fff" stroke-width="4"/></svg>
  <h3>Get your Pack</h3>
  <p>We'll send out your first pack<br>right away and then again every<br>3 or 6 months.</p>
</div>
<svg class="step-arrow" style="left:366px" width="50" height="28" viewBox="0 0 50 28"><path d="M2 14 H46 M34 3 L47 14 L34 25" fill="none" stroke="#fff" stroke-width="3"/></svg>
<svg class="step-arrow" style="left:748px" width="50" height="28" viewBox="0 0 50 28"><path d="M2 14 H46 M34 3 L47 14 L34 25" fill="none" stroke="#fff" stroke-width="3"/></svg>

<!-- plans -->
<div class="wood" style="top:1162px;height:670px" role="img" aria-label="Dark timber plank wall background"></div>
<h2 class="section-title" style="top:1212px">PLANS</h2>

<article class="plan plan--comfort">
  <div class="plan-badge">Comfort</div>
  <div class="plan-photo" role="img" aria-label="Photo of assorted trunks and briefs laid out in their packaging"></div>
  <div class="plan-option" style="top:113px">Comfort Plan 1</div>
  <div class="plan-option" style="top:172px">Comfort Plan 2</div>
  <div class="plan-price">$30</div>
  <div class="get-it">Get It</div>
</article>
<article class="plan plan--style">
  <div class="plan-badge">Style</div>
  <div class="plan-photo" role="img" aria-label="Photo of patterned dress socks fanned out on a dark surface"></div>
  <div class="plan-option" style="top:113px">Style Plan 1</div>
  <div class="plan-option" style="top:172px">Style Plan 2</div>
  <div class="plan-price">$30</div>
  <div class="get-it">Get It</div>
</article>

<div class="perks">
  <div class="perk" style="left:140px"><div class="perk-icon"><svg width="24" height="16" viewBox="0 0 24 16"><rect x="1" y="2" width="13" height="9" fill="#fff"/><path d="M14 5 H19 L23 9 V11 H14 Z" fill="#fff"/><circle cx="6" cy="13" r="2.5" fill="#fff"/><circle cx="18" cy="13" r="2.5" fill="#fff"/></svg></div>Free Shipping</div>
  <div class="perk" style="left:391px"><div class="perk-icon"><svg width="22" height="20" viewBox="0 0 22 20"><path d="M3 14 V9 Q3 5 8 5 H17 M13 1 L17 5 L13 9" fill="none" stroke="#fff" stroke-width="2.5"/></svg></div>Easy Returns</div>
  <div class="perk" style="left:645px"><div class="perk-icon"><svg width="24" height="22" viewBox="0 0 24 22"><path d="M1 3 H5 L8 14 H19 L22 6 H7" fill="none" stroke="#fff" stroke-width="2"/><circle cx="9" cy="18" r="2" fill="#fff"/><circle cx="18" cy="18" r="2" fill="#fff"/></svg></div>Cancel Whenever</div>
  <div class="perk" style="left:871px"><div class="perk-icon"><svg width="20" height="24" viewBox="0 0 20 24"><path d="M10 1 L19 5 V11 Q19 19 10 23 Q1 19 1 11 V5 Z" fill="none" stroke="#fff" stroke-width="2"/><path d="M5 12 L9 16 L15 8" fill="none" stroke="#fff" stroke-width="2"/></svg></div>Satisfication Guaranteed</div>
</div>

<!-- faq -->
<section class="faq">
  <h2 class="section-title" style="top:34px">FAQ</h2>
  <div class="faq-item" style="left:152px;top:125px"><h4>What Is Brick Dune ?</h4><p>Lorem Ipsum is simply dummy text of the printing and typesetting industry. Lorem Ipsum has been the industry's standard dummy text ever since the 1500 specimen book.</p></div>
  <div class="faq-item" style="left:460px;top:125px"><h4>What Is Shipping Policy ?</h4><p>Lorem Ipsum is simply dummy text of the printing and typesetting industry. Lorem Ipsum has been the industry's standard dummy text ever since the 1500 specimen book.</p></div>
  <div class="faq-item" style="left:778px;top:125px"><h4>What Is Your<br>Satisfication Gurantee ?</h4><p class="tight">Lorem Ipsum is simply dummy text of the printing and typesetting industry. Lorem Ipsum has been the industry's standard dummy text ever since the 1500 specimen book.</p></div>
  <div class="faq-item" style="left:152px;top:327px"><h4>What do i get with<br>My Brick Dune</h4><p class="tight">Lorem Ipsum is simply dummy text of the printing and typesetting industry. Lorem Ipsum has been the industry's standard dummy text ever since the 1500 specimen book.</p></div>
  <div class="faq-item" style="left:460px;top:327px"><h4>Returns Policy</h4><p class="tight" style="margin-top:33px">Lorem Ipsum is simply dummy text of the printing and typesetting industry. Lorem Ipsum has been the industry's standard dummy text ever since the 1500 specimen book.</p></div>
  <div class="faq-item" style="left:778px;top:327px"><h4>What Brands do you stock ?</h4><p class="tight" style="margin-top:33px">Lorem Ipsum is simply dummy text of the printing and typesetting industry. Lorem Ipsum has been the industry's standard dummy text ever since the 1500 specimen book.</p></div>
  <div class="dots"><span class="on"></span><span></span><span></span><span></span></div>
</section>

<!-- contact -->
<section class="contact">
  <h2 class="section-title">CONTACT US</h2>
  <div class="field-label" style="top:117px">Your Name *</div>
  <div class="field" style="top:151px;height:36px"></div>
  <div class="field-label" style="top:198px">Your email address *</div>
  <div class="field" style="top:231px;height:36px"></div>
  <div class="field-label" style="top:279px">Your Phone *</div>
  <div class="field" style="top:306px;height:38px"></div>
  <div class="field-label" style="top:356px">Your message</div>
  <div class="field" style="top:377px;height:130px"></div>
  <div class="submit"><svg width="8" height="10" viewBox="0 0 8 10"><path d="M2 1 L6 5 L2 9" fill="none" stroke="#fff" stroke-width="2"/></svg>SUBMIT</div>

  <div class="divider"></div>
  <div class="col-title" style="top:117px">LOCATION</div>
  <div class="map" role="img" aria-label="Street map showing the office location"></div>
  <div class="col-title" style="top:383px">OUR ADDRESS</div>
  <div class="address">Brick Dune Office<br>Harbour Lane 42b<br>2010 Surry Hills<br>Australia<br>Telephone: +61 2 5550 1234<br>E-mail: hello@brickdune.com.au</div>
</section>

<!-- footer -->
<footer class="site-footer">
  <div class="footer-links">Home<span>|</span>How It Works<span>|</span>Plans<span>|</span>FAQ<span>|</span>Contact Us</div>
  <div class="copyright">© 2014 Company Name,All Rights Reserved</div>
  <div class="footer-head" style="left:670px">Payment Options</div>
  <div class="pay-cards"><span></span><span></span><span></span><span></span><span></span></div>
  <div class="footer-head" style="left:951px">Connect With Us</div>
  <div class="socials"><span></span><span></span><span></span></div>
</footer>

</body>
</html>
```